Creative, Colorful, Dynamic Infographic for Global Non-Profit

We are a global arts and education non-profit in need of an infographic that illustrates four key skills embedded in our work: Curiosity, Listening, Imagination, Postive Action.
We work primarily with educators, students, and artists who use the power of personal stories to build community and connection and to bridge divides.
Our new brand guidelines, logos, and fonts are here: https://stylevault.example/lumen-circle
I've attached a mock-up of the graphic and the required text. (Note the attached design was created by a staff person, your final design does not need to be the same. The color scheme and text of the final design should match the brand guidelines above.)
The graphic will be used for both web and print media and should include the purple Lumen Circle logo (also attached).
Ideally the final design will delight audiences and spark interest in our work.

```html
<!DOCTYPE html>
<html lang="en">
<head>
<meta charset="utf-8">
<title>Lumen Circle – Four Key Skills</title>
<link rel="stylesheet" href="https://fonts.googleapis.com/css2?family=Libre+Franklin:wght@500;600&family=Source+Serif+4:opsz,wght@8..60,500&display=swap">
<style>
  :root {
    --page: #e4e4e4;
    --card: #ffffff;
    --ink: #16162a;
    --navy: #1f1d3f;
    --yellow: #e6c94a;
    --red: #ee4645;
    --orange: #f39856;
    --green: #52b78c;
    --white: #ffffff;
    --sans: "Libre Franklin", Arial, sans-serif;
    --serif: "Source Serif 4", Georgia, serif;
  }
  * { box-sizing: border-box; margin: 0; padding: 0; }
  html, body { width: 1200px; height: 1200px; overflow: hidden; background: var(--page); }
  .infographic {
    position: absolute; left: 0; top: 176px;
    width: 1200px; height: 848px;
    background: var(--card);
    font-family: var(--sans); font-weight: 500; color: var(--ink);
  }
  .connectors { position: absolute; inset: 0; }
  .skill {
    position: absolute; height: 93px; border-radius: 32px;
    display: flex; align-items: center; color: var(--white);
    font-family: var(--serif); font-weight: 500; font-size: 50px; line-height: 1;
    letter-spacing: -0.3px; white-space: nowrap;
    padding: 0 12px 0 20px; gap: 12px;
  }
  .skill-name { padding-bottom: 4px; }
  .skill--curiosity { left: 62px; top: 145px; width: 342px; background: var(--yellow); justify-content: space-between; }
  .skill--action { left: 690px; top: 145px; width: 454px; background: var(--red); padding-left: 12px; gap: 24px; }
  .skill--listening { left: 62px; top: 588px; width: 322px; background: var(--orange); justify-content: space-between; }
  .skill--imagination { left: 745px; top: 588px; width: 399px; background: var(--green); padding-left: 12px; gap: 26px; }
  .skill-icon { width: 70px; height: 70px; border-radius: 50%; background: var(--white); flex: none; }
  .skill-desc { position: absolute; font-size: 21px; line-height: 28px; }
  .desc--curiosity { left: 62px; top: 256px; }
  .desc--action { left: 771px; top: 251px; }
  .desc--listening { left: 62px; top: 700px; }
  .desc--imagination { left: 769px; top: 701px; }
  .bubble-text { position: absolute; font-size: 18px; line-height: 24px; }
  .bubble-text--action { left: 469px; top: 59px; }
  .bubble-text--curiosity { left: 69px; top: 419px; }
  .bubble-text--imagination { left: 902px; top: 413px; }
  .bubble-text--listening { left: 460px; top: 726px; }
  .brand {
    position: absolute; left: 480px; top: 324px; width: 238px; height: 238px;
    border-radius: 50%; background: var(--navy);
    display: flex; align-items: center; justify-content: center; text-align: center;
    color: var(--white); font-family: var(--serif); font-weight: 500; font-size: 40px; line-height: 1.1;
  }
</style>
</head>
<body>
<main class="infographic">
  <svg class="connectors" width="1200" height="848" viewBox="0 0 1200 848" fill="none" stroke-width="3" stroke-linejoin="miter">
    <g stroke-width="6">
      <path d="M596 300 A143 143 0 0 0 456 440" stroke="var(--yellow)"/>
      <path d="M602 300 A143 143 0 0 1 742 440" stroke="var(--red)"/>
      <path d="M742 446 A143 143 0 0 1 602 586" stroke="var(--green)"/>
      <path d="M596 586 A143 143 0 0 1 456 446" stroke="var(--orange)"/>
    </g>
    <path stroke="var(--red)" d="M468 52 H694 Q701 52 701 59 V125 Q701 132 694 132 H468 Q461 132 461 125 V90 L404 103 L461 74 V59 Q461 52 468 52 Z"/>
    <path stroke="var(--yellow)" d="M66 413 H288 Q295 413 295 420 V482 Q295 489 288 489 H203 L184 527 L162 489 H66 Q59 489 59 482 V420 Q59 413 66 413 Z"/>
    <path stroke="var(--green)" d="M891 407 H993 L1004 367 L1026 407 H1097 Q1104 407 1104 414 V481 Q1104 488 1097 488 H891 Q884 488 884 481 V414 Q884 407 891 407 Z"/>
    <path stroke="var(--orange)" d="M457 721 H678 Q685 721 685 728 V752 L742 749 L685 772 V791 Q685 798 678 798 H457 Q450 798 450 791 V728 Q450 721 457 721 Z"/>
  </svg>

  <div class="brand">Lumen<br>Circle</div>

  <div class="skill skill--curiosity"><span class="skill-name">Curiosity</span><span class="skill-icon" role="img" aria-label="Icon of a person thinking with question marks"></span></div>
  <div class="skill skill--action"><span class="skill-icon" role="img" aria-label="Icon of two hands clasped"></span><span class="skill-name">Positive Action</span></div>
  <div class="skill skill--listening"><span class="skill-name">Listening</span><span class="skill-icon" role="img" aria-label="Icon of an ear listening"></span></div>
  <div class="skill skill--imagination"><span class="skill-icon" role="img" aria-label="Icon of a head with sparkles"></span><span class="skill-name">Imagination</span></div>

  <p class="skill-desc desc--curiosity">Focus On How You Can Learn<br>From Others' Knowledge And<br>Experience.</p>
  <p class="skill-desc desc--action">Show That Your Words And Actions<br>Matter.</p>
  <p class="skill-desc desc--listening">Work To Understand Before<br>Using Words.</p>
  <p class="skill-desc desc--imagination">Consider Possibilities Beyond What<br>You Already Know.</p>

  <p class="bubble-text bubble-text--action">Your positive actions will<br>make you curious about<br>what else is possible.</p>
  <p class="bubble-text bubble-text--curiosity">Your curiosity will allow<br>you to listen.</p>
  <p class="bubble-text bubble-text--imagination">Your imagination<br>identifies positive<br>actions.</p>
  <p class="bubble-text bubble-text--listening">Your listening will allow<br>you to take in new<br>information.</p>
</main>
</body>
</html>
```